Redesign Website - Current one too plain

The description is in the uploaded file. Please let me know if you need any more information. I'd prefer it if someone could implement the design to a WordPress site but the best design will win, regardless.
I would like the forms to look nice as well
UPDATE:
I don't think we can use the images that I provided, I think they make the site look a bit 'cheap' and I really don't know how to replace them. One thought I have had is to make the "Simple, Unique, Effective" a second feature on the right side of the page with the search on the left
Target Market(s)
Small companies, private sellers of cars and people who rent their caravan/holiday home out
Industry/Entity Type
Advertising
Number of Pages Required
3 page
Colors
Designer to choose colors to be used in the design.
Look and feel
Each slider illustrates characteristics of the customer's brand and the style your logo design should communicate.

```html
<!DOCTYPE html>
<html lang="en">
<head>
<meta charset="utf-8">
<title>Vantrio – Website Redesign</title>
<link rel="stylesheet" href="https://fonts.googleapis.com/css2?family=Poppins:wght@400;500;600;700&display=swap">
<style>
:root{
  --neon:#e2ff00;
  --ink:#2b2b2b;
  --dark:#333333;
  --muted:#9a9a9a;
  --field:#eeeeee;
  --panel:#efefef;
  --white:#ffffff;
  --backdrop-top:#3f3f3f;
  --backdrop-bottom:#262626;
}
*{box-sizing:border-box;margin:0;padding:0}
html,body{width:1188px;height:1200px;overflow:hidden}
body{font-family:"Poppins",sans-serif;color:var(--ink);background:var(--backdrop-bottom)}
.board{position:relative;width:1188px;height:1200px;overflow:hidden}
.backdrop{position:absolute;inset:0;background:linear-gradient(180deg,var(--backdrop-top) 0%,#383838 35%,#4a4744 55%,var(--backdrop-bottom) 100%)}
.band{position:absolute;inset:0}
.brand-hero{position:absolute;left:0;top:100px;width:1188px;display:flex;align-items:center;justify-content:center;gap:22px}
.brand-hero .dot{width:56px;height:56px;border-radius:50%;background:var(--neon)}
.brand-hero .name{font-size:58px;font-weight:500;letter-spacing:0;color:var(--white);line-height:1}

.screen{position:absolute;width:466px;background:var(--white);box-shadow:0 10px 30px rgba(0,0,0,.35);overflow:hidden}
.screen *{position:absolute}
.site-header{left:0;top:0;width:100%;height:39px;background:var(--white)}
.site-logo{left:35px;top:11px;display:flex;align-items:center;gap:5px;position:absolute}
.site-logo .mark{position:static;width:10px;height:10px;border-radius:50%;background:var(--neon)}
.site-logo .word{position:static;font-size:13px;font-weight:500;letter-spacing:0;color:var(--ink);line-height:1}
.nav{top:14px;font-size:4.6px;font-weight:500;text-transform:uppercase;display:flex;align-items:center;gap:2px;color:var(--ink)}
.nav svg{position:static;width:6px;height:6px}
.nav.active{font-weight:700}
.nav-sep{top:12px;width:1px;height:10px;background:#e3e3e3}
.cta{left:352px;top:9px;width:79px;height:16px;background:var(--neon);border-radius:2px;font-size:4.4px;font-weight:700;display:flex;align-items:center;justify-content:center;text-transform:uppercase}

.footer-rule{left:35px;width:396px;height:1px;background:#e2e2e2}
.copyright{left:0;width:100%;text-align:center;font-size:5.2px;font-weight:500}
.to-top{width:15px;height:15px;border-radius:3px;background:var(--dark);display:flex;align-items:center;justify-content:center}
.to-top svg{position:static;width:5px;height:5px}

.page-bg{left:0;top:39px;width:100%;background:var(--panel)}
.page-title{left:0;width:100%;text-align:center;font-size:16.5px;font-weight:700;line-height:1}
.page-sub{left:0;width:100%;text-align:center;font-size:5.2px}
.perks{left:0;top:93px;width:100%;display:flex;justify-content:center;gap:7px;font-size:5.2px}
.perks span{position:static;display:flex;align-items:center;gap:4px}
.perks i{position:static;width:9px;height:9px;border-radius:50%;background:#f3f8d0;display:flex;align-items:center;justify-content:center}
.perks i svg{position:static;width:5px;height:5px}

.form-card{background:var(--white);border-radius:10px;box-shadow:0 3px 12px rgba(0,0,0,.05)}
.form-card.accent{border-bottom:1.5px solid var(--neon)}
.label{font-size:3.8px;font-weight:500;text-transform:uppercase;white-space:nowrap}
.label b{position:static;color:var(--neon);font-weight:500}
.field{background:var(--field);border-radius:2px;font-size:4px;color:var(--muted);padding:5px 8px;white-space:nowrap}
.hint{font-size:3.8px;color:var(--muted);white-space:nowrap}
.radios{display:flex;gap:15px;font-size:4px;color:var(--muted)}
.radios span{position:static;display:flex;align-items:center;gap:2px}
.radios i{position:static;width:3.5px;height:3.5px;border:0.8px solid var(--ink);border-radius:50%}
.upload{border:0.8px dashed #cfcfcf;border-radius:3px;text-align:center}
.upload .icon{left:89px;top:12px;width:15px;height:14px;background:var(--dark);border-radius:2px;display:flex;align-items:center;justify-content:center}
.upload .icon svg{position:static;width:6px;height:6px}
.upload .note{left:0;top:30px;width:100%;font-size:3.8px;color:var(--muted);line-height:1.7}
.submit{height:17px;background:var(--neon);border-radius:2px;font-size:5px;font-weight:700;display:flex;align-items:center;justify-content:center;box-shadow:0 1.5px 0 #b9d100}

.hero-photo{left:0;top:34px;width:100%;height:296px;background:linear-gradient(180deg,#e6e8ea 0%,#cfd3d6 35%,#8d8b80 55%,#7b7f80 75%,#c9cccf 100%)}
.search-card{left:64px;top:97px;width:133px;height:147px;background:var(--white);border-radius:8px;border-top:1.5px solid var(--neon);box-shadow:0 4px 14px rgba(0,0,0,.15)}
.code{left:0;top:18px;width:100%;text-align:center;font-size:48px;font-weight:700;letter-spacing:2px;line-height:1}
.chev{width:6px;height:4px}
.type-btn{top:87px;width:36px;height:13px;background:var(--field);border-radius:2px;font-size:4.3px;font-weight:600;display:flex;align-items:center;justify-content:center}
.search-btn{left:11px;top:110px;width:111px;height:17px;background:var(--neon);border-radius:2px;font-size:4.5px;font-weight:700;display:flex;align-items:center;justify-content:center;box-shadow:0 1.5px 0 #b9d100}
.feature{top:307px;width:93px;height:94px;background:var(--white);border-radius:8px;box-shadow:0 4px 14px rgba(0,0,0,.1);text-align:center}
.feature svg{left:32px;top:9px;width:29px;height:29px}
.feature h3{left:0;top:46px;width:100%;font-size:9px;font-weight:700;line-height:1}
.feature p{left:10px;top:60px;width:73px;font-size:4.9px;line-height:1.4}
</style>
</head>
<body>
<main class="board">
  <div class="backdrop" role="img" aria-label="Dark misty mountain landscape with a road in the foreground"></div>
  <svg class="band" viewBox="0 0 1188 1200" aria-hidden="true"><polygon points="1188,242 1188,497 0,1161 0,904" fill="#e2ff00"/></svg>

  <div class="brand-hero"><span class="dot"></span><span class="name">Vantrio</span></div>

  <!-- Create advert page -->
  <section class="screen" style="left:602px;top:250px;height:454px">
    <header class="site-header">
      <div class="site-logo"><span class="mark"></span><span class="word">Vantrio</span></div>
      <span class="nav" style="left:180px"><svg viewBox="0 0 10 10"><path d="M1 5 5 1l4 4H8v4H2V5z" fill="#2b2b2b"/></svg>Home</span>
      <span class="nav-sep" style="left:213px"></span>
      <span class="nav" style="left:222px"><svg viewBox="0 0 10 10"><rect x="1" y="1" width="8" height="8" fill="none" stroke="#2b2b2b"/></svg>Contact</span>
      <span class="nav-sep" style="left:263px"></span>
      <span class="nav" style="left:272px"><svg viewBox="0 0 10 10"><circle cx="4" cy="3" r="2" fill="none" stroke="#2b2b2b"/><path d="M1 9c0-3 6-3 6 0" fill="none" stroke="#2b2b2b"/></svg>Register</span>
      <span class="nav-sep" style="left:312px"></span>
      <span class="nav" style="left:320px"><svg viewBox="0 0 10 10"><circle cx="5" cy="3" r="2" fill="none" stroke="#2b2b2b"/><path d="M1 9c0-3 8-3 8 0" fill="none" stroke="#2b2b2b"/></svg>Login</span>
      <span class="cta">Advertise your company</span>
    </header>
    <div class="page-bg" style="height:296px"></div>
    <h1 class="page-title" style="top:68px">Create Your Advert</h1>
    <div class="perks">
      <span><i><svg viewBox="0 0 10 10"><path d="M1 5l3 3 5-6" fill="none" stroke="#c9e600" stroke-width="2"/></svg></i>Free to advertise</span>
      <span><i><svg viewBox="0 0 10 10"><path d="M1 5l3 3 5-6" fill="none" stroke="#c9e600" stroke-width="2"/></svg></i>Free graphics to print and display</span>
      <span><i><svg viewBox="0 0 10 10"><path d="M1 5l3 3 5-6" fill="none" stroke="#c9e600" stroke-width="2"/></svg></i>Weatherproof vinyl graphics available</span>
    </div>
    <form class="form-card accent" style="left:102px;top:120px;width:262px;height:273px">
      <p style="left:0;top:14px;width:100%;text-align:center;font-size:5px"><b style="position:static;font-weight:600">Login</b> or <b style="position:static;font-weight:600">Register</b> to create your advert</p>
      <span class="label" style="left:35px;top:37px">Compan name, make/model of car, etc <b>*</b></span>
      <span class="field" style="left:35px;top:45px;width:192px;height:15px"></span>
      <div class="radios" style="left:35px;top:64px"><span><i></i>Car</span><span><i></i>Company</span><span><i></i>Holiday</span></div>
      <span class="label" style="left:35px;top:80px">Town/city, county or area <b>*</b></span>
      <span class="label" style="left:133px;top:80px">Website or social media page <b>*</b></span>
      <span class="field" style="left:35px;top:88px;width:94px;height:15px"></span>
      <span class="field" style="left:133px;top:88px;width:94px;height:15px"></span>
      <span class="label" style="left:35px;top:112px">Description <b>*</b></span>
      <span class="field" style="left:35px;top:120px;width:192px;height:37px"></span>
      <span class="hint" style="left:180px;top:160px">0 of 4000 max characters</span>
      <span class="label" style="left:35px;top:166px">Upload photo</span>
      <div class="upload" style="left:35px;top:174px;width:192px;height:53px">
        <span class="icon"><svg viewBox="0 0 10 10"><path d="M5 7V1M2 4l3-3 3 3M1 8v1h8V8" fill="none" stroke="#e2ff00" stroke-width="1.2"/></svg></span>
        <span class="note">Upload images - select main image first<br>Maximum Upload size: 10 MB</span>
      </div>
      <span class="submit" style="left:105px;top:240px;width:53px">SUBMIT</span>
    </form>
    <span class="footer-rule" style="top:430px"></span>
    <span class="to-top" style="left:442px;top:422px"><svg viewBox="0 0 10 10"><path d="M2 7l3-3 3 3" fill="none" stroke="#e2ff00" stroke-width="1.5"/></svg></span>
    <p class="copyright" style="top:438px">© Copyright 2023 Vantrio. All Rights Reserved</p>
  </section>

  <!-- Contact page -->
  <section class="screen" style="left:602px;top:730px;height:382px">
    <header class="site-header">
      <div class="site-logo"><span class="mark"></span><span class="word">Vantrio</span></div>
      <span class="nav" style="left:180px"><svg viewBox="0 0 10 10"><path d="M1 5 5 1l4 4H8v4H2V5z" fill="#2b2b2b"/></svg>Home</span>
      <span class="nav-sep" style="left:213px"></span>
      <span class="nav" style="left:222px"><svg viewBox="0 0 10 10"><rect x="1" y="1" width="8" height="8" fill="none" stroke="#2b2b2b"/></svg>Contact</span>
      <span class="nav-sep" style="left:263px"></span>
      <span class="nav" style="left:272px"><svg viewBox="0 0 10 10"><circle cx="4" cy="3" r="2" fill="none" stroke="#2b2b2b"/><path d="M1 9c0-3 6-3 6 0" fill="none" stroke="#2b2b2b"/></svg>Register</span>
      <span class="nav-sep" style="left:312px"></span>
      <span class="nav" style="left:320px"><svg viewBox="0 0 10 10"><circle cx="5" cy="3" r="2" fill="none" stroke="#2b2b2b"/><path d="M1 9c0-3 8-3 8 0" fill="none" stroke="#2b2b2b"/></svg>Login</span>
      <span class="cta">Advertise your company</span>
    </header>
    <div class="page-bg" style="height:234px"></div>
    <h1 class="page-title" style="top:68px">Contact Us</h1>
    <p class="page-sub" style="top:88px">We can help, our team of experts is on hand to answer your questions.</p>
    <form class="form-card" style="left:119px;top:110px;width:228px;height:201px">
      <span class="label" style="left:17px;top:20px">Name <b>*</b></span>
      <span class="field" style="left:17px;top:27px;width:193px;height:16px">Enter your name</span>
      <span class="label" style="left:17px;top:50px">Email <b>*</b></span>
      <span class="label" style="left:115px;top:50px">Phone <b>*</b></span>
      <span class="field" style="left:17px;top:58px;width:95px;height:16px">Enter your email</span>
      <span class="field" style="left:115px;top:58px;width:95px;height:16px">Enter your phone number</span>
      <span class="label" style="left:17px;top:80px">Message <b>*</b></span>
      <span class="field" style="left:17px;top:88px;width:193px;height:51px">Type your text</span>
      <span class="hint" style="left:163px;top:143px">0 of 4000 max characters</span>
      <span class="submit" style="left:88px;top:158px;width:53px">SUBMIT</span>
    </form>
    <span class="footer-rule" style="top:356px"></span>
    <span class="to-top" style="left:442px;top:348px"><svg viewBox="0 0 10 10"><path d="M2 7l3-3 3 3" fill="none" stroke="#e2ff00" stroke-width="1.5"/></svg></span>
    <p class="copyright" style="top:365px">© Copyright 2023 Vantrio. All Rights Reserved</p>
  </section>

  <!-- Home page -->
  <section class="screen" style="left:113px;top:492px;height:454px">
    <header class="site-header" style="height:34px">
      <div class="site-logo" style="top:10px"><span class="mark"></span><span class="word">Vantrio</span></div>
      <span class="nav active" style="left:180px;top:14px"><svg viewBox="0 0 10 10"><path d="M1 5 5 1l4 4H8v4H2V5z" fill="#2b2b2b"/></svg>Home</span>
      <span class="nav-sep" style="left:213px;top:12px"></span>
      <span class="nav" style="left:222px;top:14px"><svg viewBox="0 0 10 10"><rect x="1" y="1" width="8" height="8" fill="none" stroke="#2b2b2b"/></svg>Contact</span>
      <span class="nav-sep" style="left:263px;top:12px"></span>
      <span class="nav" style="left:272px;top:14px"><svg viewBox="0 0 10 10"><circle cx="4" cy="3" r="2" fill="none" stroke="#2b2b2b"/><path d="M1 9c0-3 6-3 6 0" fill="none" stroke="#2b2b2b"/></svg>Register</span>
      <span class="nav-sep" style="left:312px;top:12px"></span>
      <span class="nav" style="left:320px;top:14px"><svg viewBox="0 0 10 10"><circle cx="5" cy="3" r="2" fill="none" stroke="#2b2b2b"/><path d="M1 9c0-3 8-3 8 0" fill="none" stroke="#2b2b2b"/></svg>Login</span>
      <span class="cta">Advertise your company</span>
    </header>
    <div class="hero-photo" role="img" aria-label="White SUV with a code sticker parked by icy water below snowy mountains"></div>
    <div class="search-card">
      <svg class="chev" style="left:42px;top:16px" viewBox="0 0 6 4"><path d="M0.5 3.5 3 1l2.5 2.5" fill="none" stroke="#888" stroke-width=".8"/></svg>
      <svg class="chev" style="left:76px;top:16px" viewBox="0 0 6 4"><path d="M0.5 3.5 3 1l2.5 2.5" fill="none" stroke="#888" stroke-width=".8"/></svg>
      <span class="code">A1</span>
      <svg class="chev" style="left:42px;top:69px" viewBox="0 0 6 4"><path d="M0.5 0.5 3 3l2.5-2.5" fill="none" stroke="#888" stroke-width=".8"/></svg>
      <svg class="chev" style="left:76px;top:69px" viewBox="0 0 6 4"><path d="M0.5 0.5 3 3l2.5-2.5" fill="none" stroke="#888" stroke-width=".8"/></svg>
      <span class="type-btn" style="left:11px">CAR</span>
      <span class="type-btn" style="left:49px">CARAVAN</span>
      <span class="type-btn" style="left:87px">COMPANY</span>
      <span class="search-btn">SEARCH</span>
    </div>
    <article class="feature" style="left:86px">
      <svg viewBox="0 0 30 30"><path d="M4 27 17 14" stroke="#2b2b2b" stroke-width="2"/><path d="M20 5l2 5 5 1-4 3 1 5-4-3-4 3 1-5-4-3 5-1z" fill="#e2ff00" stroke="#2b2b2b" stroke-width="1"/></svg>
      <h3>Simple</h3>
      <p>Create your advert and display your code</p>
    </article>
    <article class="feature" style="left:186px">
      <svg viewBox="0 0 30 30"><circle cx="15" cy="12" r="10" fill="none" stroke="#2b2b2b" stroke-width="1.2"/><circle cx="15" cy="12" r="6" fill="none" stroke="#2b2b2b" stroke-width="1.2"/><rect x="12" y="12" width="6" height="15" rx="3" fill="#e2ff00" stroke="#2b2b2b"/></svg>
      <h3>Unique</h3>
      <p>Customers find you by an easy-to-remember code</p>
    </article>
    <article class="feature" style="left:287px">
      <svg viewBox="0 0 30 30"><circle cx="13" cy="17" r="11" fill="none" stroke="#2b2b2b" stroke-width="1.2"/><circle cx="13" cy="17" r="7" fill="#e2ff00" stroke="#2b2b2b"/><circle cx="13" cy="17" r="3" fill="none" stroke="#2b2b2b"/><path d="M13 17 27 3M23 3h4v4" fill="none" stroke="#2b2b2b" stroke-width="1.2"/></svg>
      <h3>Effective</h3>
      <p>Customers are directed to you and not a list of your competitors</p>
    </article>
    <span class="footer-rule" style="top:428px"></span>
    <span class="to-top" style="left:441px;top:421px"><svg viewBox="0 0 10 10"><path d="M2 7l3-3 3 3" fill="none" stroke="#e2ff00" stroke-width="1.5"/></svg></span>
    <p class="copyright" style="top:437px">© Copyright 2023 Vantrio. All Rights Reserved</p>
  </section>
</main>
</body>
</html>
```